Pinecrest Lantern Studio STATIONARY
business cards and letterhead
Professional
Lyle Poniatwicz
President
2417 Marlow Avenue
Fenwick Harbour, Northvale
L3R 8T1
lyle@pinecrestlanternstudio.ca
pinecrestlanternstudio.ca

```html
<!DOCTYPE html>
<html lang="en">
<head>
<meta charset="utf-8">
<title>Pinecrest Lantern Studio Stationery</title>
<link rel="stylesheet" href="https://fonts.googleapis.com/css2?family=Michroma&family=Open+Sans:wght@400;600&display=swap">
<style>
:root{
  --bg:#e9eaec;
  --paper:#ffffff;
  --ink:#111317;
  --ink-soft:#2a2d33;
  --blue:#1aa6ec;
  --blue-deep:#0b7fc7;
  --steel:#8e959c;
  --steel-light:#cfd3d7;
  --text:#4a4f55;
}
*{margin:0;padding:0;box-sizing:border-box}
html,body{width:1200px;height:936px;overflow:hidden;background:var(--bg)}
body{position:relative;font-family:"Open Sans",Arial,sans-serif;color:var(--text)}
.piece{position:absolute;overflow:hidden;background:var(--paper);box-shadow:0 2px 6px rgba(0,0,0,.12)}
.piece svg.art{position:absolute;inset:0;width:100%;height:100%}
.brand{position:absolute;display:flex;align-items:center;gap:8px}
.brand-dot{border-radius:50%;background:var(--blue);flex:none}
.brand-name{font-family:"Michroma",Arial,sans-serif;letter-spacing:.04em;line-height:1.15;text-transform:uppercase}

/* letterhead */
.letterhead{left:183px;top:56px;width:395px;height:558px}
.letterhead .brand{left:22px;top:14px}
.letterhead .brand-dot{width:30px;height:30px}
.letterhead .brand-name{font-size:10px;color:var(--ink-soft)}
.contact{position:absolute;left:24px;bottom:26px;list-style:none;font-size:6.5px;line-height:11px}
.contact li{display:flex;align-items:center;gap:5px}
.contact .ico{width:7px;height:7px;border-radius:50%;background:var(--blue-deep);flex:none}
.contact .ico.spacer{visibility:hidden}

/* folder */
.folder{left:634px;top:38px;width:462px;height:584px;background:var(--ink)}
.folder .brand{left:62px;top:252px;gap:14px}
.folder .brand-dot{width:60px;height:60px}
.folder .brand-name{font-size:19px;color:#fff}

/* business cards */
.card{width:182px;height:96px;background:var(--ink)}
.card-front{left:41px;top:655px}
.card-back{left:41px;top:779px}
.card-front .brand{left:10px;top:9px;gap:5px}
.card-front .brand-dot{width:17px;height:17px}
.card-front .brand-name{font-size:6px;color:#fff}
.card-front .person{position:absolute;right:12px;bottom:18px;text-align:right;font-size:5px;line-height:7px;color:var(--ink-soft)}
.card-front .person strong{font-weight:600}
.card-back .brand-dot{position:absolute;left:75px;top:26px;width:32px;height:32px}
.card-back .web{position:absolute;left:0;right:0;bottom:9px;text-align:center;font-size:5px;letter-spacing:.25em;color:#9aa1a8}

/* envelopes */
.envelope{top:672px;height:203px}
.envelope-front{left:261px;width:439px}
.envelope-front .brand{left:14px;top:10px;gap:6px}
.envelope-front .brand-dot{width:22px;height:22px}
.envelope-front .brand-name{font-size:7px;color:#fff}
.envelope-front .return{position:absolute;left:44px;top:36px;font-size:5px;line-height:7px;color:#c9ced3}
.envelope-back{left:738px;width:434px}
.envelope-back .web{position:absolute;left:0;right:0;top:14px;text-align:center;font-size:8px;letter-spacing:.42em;color:#fff}
</style>
</head>
<body>

<section class="piece letterhead" aria-label="Letterhead">
  <svg class="art" viewBox="0 0 395 558" preserveAspectRatio="none">
    <path d="M0 64 Q200 60 395 30 L395 46 Q210 74 0 78 Z" fill="var(--blue)"/>
    <path d="M0 80 Q210 76 395 49 L395 52 Q210 80 0 83 Z" fill="var(--steel-light)"/>
  </svg>
  <div class="brand">
    <span class="brand-dot"></span>
    <span class="brand-name">Pinecrest Lantern<br>Studio</span>
  </div>
  <ul class="contact">
    <li><span class="ico"></span>2417 Marlow Avenue, Fenwick Harbour</li>
    <li><span class="ico spacer"></span>Northvale L3R 8T1</li>
    <li><span class="ico"></span>905 555-0148</li>
    <li><span class="ico"></span>lyle@pinecrestlanternstudio.ca</li>
    <li><span class="ico"></span>www.pinecrestlanternstudio.ca</li>
  </ul>
</section>

<section class="piece folder" aria-label="Presentation folder">
  <svg class="art" viewBox="0 0 462 584" preserveAspectRatio="none">
    <defs>
      <linearGradient id="folderSteel" x1="0" y1="0" x2="1" y2="0">
        <stop offset="0" stop-color="#5d6369"/><stop offset=".5" stop-color="#c4c9ce"/><stop offset="1" stop-color="#70767c"/>
      </linearGradient>
    </defs>
    <path d="M0 478 Q230 452 462 494 L462 520 Q230 486 0 508 Z" fill="url(#folderSteel)"/>
    <path d="M0 508 Q230 486 462 520 L462 584 L0 584 Z" fill="var(--blue)"/>
  </svg>
  <div class="brand">
    <span class="brand-dot"></span>
    <span class="brand-name">Pinecrest Lantern<br>Studio</span>
  </div>
</section>

<section class="piece card card-front" aria-label="Business card front">
  <svg class="art" viewBox="0 0 182 96" preserveAspectRatio="none">
    <path d="M0 44 Q90 40 182 28 L182 96 L0 96 Z" fill="var(--blue)"/>
    <path d="M0 50 Q90 46 182 34 L182 96 L0 96 Z" fill="var(--paper)"/>
  </svg>
  <div class="brand">
    <span class="brand-dot"></span>
    <span class="brand-name">Pinecrest Lantern<br>Studio</span>
  </div>
  <div class="person"><strong>Lyle Poniatwicz</strong><br>President<br>lyle@pinecrestlanternstudio.ca</div>
</section>

<section class="piece card card-back" aria-label="Business card back">
  <span class="brand-dot"></span>
  <div class="web">www.pinecrestlanternstudio.ca</div>
</section>

<section class="piece envelope envelope-front" aria-label="Envelope front">
  <svg class="art" viewBox="0 0 439 203" preserveAspectRatio="none">
    <path d="M0 0 L439 0 L439 16 Q220 52 0 58 Z" fill="var(--ink)"/>
    <path d="M0 58 Q220 52 439 16 L439 30 Q220 64 0 70 Z" fill="var(--blue)"/>
  </svg>
  <div class="brand">
    <span class="brand-dot"></span>
    <span class="brand-name">Pinecrest Lantern Studio</span>
  </div>
  <div class="return">2417 Marlow Avenue, Fenwick Harbour<br>Northvale L3R 8T1</div>
</section>

<section class="piece envelope envelope-back" aria-label="Envelope back">
  <svg class="art" viewBox="0 0 434 203" preserveAspectRatio="none">
    <rect x="0" y="0" width="434" height="4" fill="var(--ink)"/>
    <rect x="0" y="4" width="434" height="34" fill="var(--blue)"/>
    <rect x="0" y="38" width="434" height="2" fill="var(--blue-deep)"/>
  </svg>
  <div class="web">www.pinecrestlanternstudio.ca</div>
</section>

</body>
</html>
```